Flyer Design Project

We need a flyer for a new company in the UK. We are selling parcels against Crown Courier, new exciting venture with better pricing and more convenience than the standard postal offering. Our colors are green and white and blue check out our website www.sendwidebox-example.com

We want to highlight our convenience and savings...

Target Market(s)

Normally expat living in the UK sending parcels home

Industry/Entity Type

It Company

```html
<!DOCTYPE html>
<html lang="en">
<head>
<meta charset="utf-8">
<title>SendWideBox – Low-Cost International Parcel Delivery</title>
<link href="https://fonts.googleapis.com/css2?family=Carlito:wght@400;700&family=Source+Sans+3:wght@400;600;700&family=Oswald:wght@500;600&display=swap" rel="stylesheet">
<style>
  :root {
    --stage: #e9e6e1;
    --ink: #111111;
    --black: #050505;
    --cyan: #29abe2;
    --blue: #1fa3dc;
    --green: #4cae3c;
    --lime: #9cc92f;
    --grey-head: #6d6e70;
    --navy: #0d2f52;
    --white: #ffffff;
    --photo-a: #c9b79c;
    --photo-b: #8fa6b8;
  }
  * { margin: 0; padding: 0; box-sizing: border-box; }
  html, body { width: 1200px; height: 900px; overflow: hidden; }
  body { background: var(--stage); font-family: "Carlito", Calibri, sans-serif; color: var(--ink); }

  .flyer {
    position: absolute; left: 247px; top: 14px; width: 608px; height: 864px;
    background: var(--white); overflow: hidden;
    box-shadow: 0 4px 14px rgba(0,0,0,.35);
  }
  .flyer-shapes { position: absolute; inset: 0; }

  .brand { position: absolute; left: 16px; top: 22px; width: 312px; }
  .brand-mark { position: absolute; left: 0; top: 4px; width: 52px; height: 52px; border-radius: 50%; background: var(--cyan); }
  .brand-name { position: absolute; left: 62px; top: 6px; font-family: "Source Sans 3", Arial, sans-serif; font-size: 29px; font-weight: 700; color: var(--white); letter-spacing: -.3px; }
  .brand-tagline { position: absolute; right: 0; top: 48px; font-family: "Source Sans 3", Arial, sans-serif; font-size: 16px; color: #cfcfcf; }

  .header-divider { position: absolute; left: 338px; top: 28px; width: 1px; height: 56px; background: #777; }
  .service-title { position: absolute; left: 353px; top: 28px; color: var(--cyan); font-weight: 700; line-height: 1; }
  .service-title .line-1 { display: block; font-size: 20px; }
  .service-title .line-2 { display: block; font-size: 29px; margin-top: 2px; }

  .visions-title {
    position: absolute; left: 0; width: 608px; top: 494px; text-align: center;
    font-family: "Oswald", Impact, sans-serif; font-weight: 600; font-size: 27px; color: var(--green); letter-spacing: .3px;
  }
  .visions-text { position: absolute; left: 18px; top: 528px; width: 575px; font-size: 16.5px; line-height: 20.5px; color: var(--ink); }

  .convenience {
    position: absolute; left: 20px; top: 632px;
    font-family: "Oswald", Impact, sans-serif; font-weight: 600; font-size: 24px; line-height: 29px; color: var(--grey-head);
  }
  .convenience .highlight { color: var(--green); }

  .prices { position: absolute; left: 30px; top: 732px; width: 290px; text-align: center; font-size: 15px; font-weight: 700; line-height: 20px; }
  .prices .dot { display: inline-block; width: 8px; height: 8px; border-radius: 50%; background: var(--green); margin: 0 4px 1px; }

  .savings {
    position: absolute; left: 352px; top: 633px;
    font-family: "Oswald", Impact, sans-serif; font-weight: 600; color: var(--white); font-size: 22px; line-height: 31px; letter-spacing: .2px;
  }
  .savings .big { font-size: 29px; }

  .contact { position: absolute; right: 18px; top: 767px; text-align: right; font-size: 13px; line-height: 15.4px; color: var(--navy); font-style: normal; }

  .social { position: absolute; left: 8px; top: 820px; width: 230px; text-align: right; font-size: 13px; line-height: 15px; color: var(--navy); }
  .social-badge { position: absolute; top: 818px; width: 44px; height: 32px; border-radius: 4px; background: var(--white); opacity: .85; }
  .social-badge.first { left: 246px; }
  .social-badge.second { left: 303px; }
</style>
</head>
<body>
  <main class="flyer">
    <svg class="flyer-shapes" viewBox="0 0 608 864" width="608" height="864" aria-hidden="true">
      <defs>
        <linearGradient id="photoTone" x1="0" y1="0" x2="1" y2="1">
          <stop offset="0" stop-color="#c9b79c"/>
          <stop offset="1" stop-color="#8fa6b8"/>
        </linearGradient>
        <linearGradient id="panelTone" x1="0" y1="0" x2="0" y2="1">
          <stop offset="0" stop-color="#e6e7e8"/>
          <stop offset=".25" stop-color="#ffffff"/>
        </linearGradient>
      </defs>
      <rect class="header-band" x="0" y="0" width="608" height="175" fill="var(--black)"/>
      <rect x="0" y="470" width="608" height="394" fill="url(#panelTone)"/>
    </svg>

    <svg class="flyer-shapes" viewBox="0 0 608 864" width="608" height="864">
      <path role="img" aria-label="Photo: smiling courier handing a parcel to a customer at her front door"
            d="M0,178 Q260,98 608,150 L608,505 Q300,470 0,510 Z" fill="url(#photoTone)"/>
    </svg>

    <svg class="flyer-shapes" viewBox="0 0 608 864" width="608" height="864" aria-hidden="true">
      <!-- top swoosh -->
      <path d="M0,155 Q250,80 608,128 L608,146 Q260,95 0,170 Z" fill="var(--cyan)"/>
      <path d="M0,170 Q260,95 608,146 L608,153 Q260,103 0,180 Z" fill="var(--lime)"/>
      <path d="M0,180 Q260,103 608,153 L608,156 Q260,107 0,183 Z" fill="var(--white)"/>
      <!-- photo bottom swoosh -->
      <path d="M0,510 Q300,470 608,505 L608,470 Q420,470 330,484 Q200,478 0,510 Z" fill="var(--white)"/>
      <path d="M300,488 Q460,462 608,475 L608,530 Q470,485 300,488 Z" fill="var(--blue)"/>
      <!-- footer band: rises to the right behind the savings panel -->
      <path d="M0,782 Q300,812 608,730 L608,864 L0,864 Z" fill="var(--lime)"/>
      <path d="M0,791 Q300,820 608,738 L608,864 L0,864 Z" fill="var(--white)"/>
      <path d="M0,796 Q300,826 608,744 L608,864 L0,864 Z" fill="var(--blue)"/>
      <!-- savings panel -->
      <path d="M343,635 Q343,621 357,621 L608,621 L608,698 Q540,765 343,770 Z" fill="var(--blue)"/>
      <path d="M343,770 Q540,765 608,698 L608,702 Q540,769 343,774 Z" fill="var(--white)"/>
      <path d="M343,774 Q540,769 608,702 L608,710 Q540,777 343,782 Z" fill="var(--lime)"/>
    </svg>

    <header>
      <div class="brand">
        <span class="brand-mark"></span>
        <span class="brand-name">SendWideBox.com</span>
        <span class="brand-tagline">Click. Ship. Smile.</span>
      </div>
      <div class="header-divider"></div>
      <h1 class="service-title">
        <span class="line-1">LOW-COST INTERNATIONAL</span>
        <span class="line-2">PARCEL DELIVERY</span>
      </h1>
    </header>

    <section>
      <h2 class="visions-title">OUR VISIONS</h2>
      <p class="visions-text">Most companies are focused on the large shippers and forget about little guys. At SendWideBox we believe that everyone should have access to cheap international parcel shipping and large shipping discounts. Paying less for your shipping means you can buy more expensive gifts for family and friends or spend it on a pint at the local – your choice!!</p>
    </section>

    <section>
      <p class="convenience">DROP TO 4500+LOCATIONS<br>OPEN EARLY TO LATE<br><span class="highlight">EASY PEASY!</span></p>
      <p class="prices">USA FROM £50.50 <span class="dot"></span> ASIA FROM £14.50<br>ROW FROM £15.50</p>
    </section>

    <section>
      <p class="savings">SAVE UPTO <span class="big">60%</span> ON<br>INTERNATIONAL PARCELS<br>HOLY SHIPS!</p>
    </section>

    <footer>
      <address class="contact">
        Contact Us :<br>
        SendWideBox Ltd.<br>
        Unit 4, Fernhill Trade Park<br>
        Wexley, Oakshire, WX9 2PL<br>
        Tel: 01632 960481<br>
        Email: cs@sendwidebox-example.com
      </address>
      <p class="social">Delivering you Posts and Status Updates<br>Be Social and Follow Us.</p>
      <span class="social-badge first"></span>
      <span class="social-badge second"></span>
    </footer>
  </main>
</body>
</html>
```